Modern Business Card for Larkwell 2018

Our company assumes the best about people. We are creating an online community of entrepreneurs and business leaders who struggle with marketing their business online.

This business card should POP! We recently got a new logo and are launching a new website next month, so our business cards should make a statement that feels:
-Fresh
-Smart
-Trustworthy
-Fun

Target Market(s)

small business owners, entrepreneurs

Industry/Entity Type

Digital Marketing

Contact Information for Business Card

Dimensions: 3.5" x 2"

Font styles to use
Sans Serif

Colors
f37122
ffffff

Requirements
Must have
• We need a business card with a modern, bold design. We will use one side of the card as a lead-generation offer, so text on one side will need to fit up to 140 characters. The business card should stick to our core colors (orange, black, and white).
Nice to have
• We think a vertical "portrait" design could be interesting.
Should not have
• Should not look like a traditional business card. The round icon should stand out from a distance.

```html
<!DOCTYPE html>
<html lang="en">
<head>
<meta charset="utf-8">
<title>Larkwell Business Card</title>
<link rel="stylesheet" href="https://fonts.googleapis.com/css2?family=Roboto:wght@400;500;700;900&family=Roboto+Condensed:wght@500;700&display=swap">
<style>
  :root {
    --orange: #f36a26;
    --white: #ffffff;
    --paper: #f2f2f2;
    --ink: #1f1f1f;
    --backdrop: #262626;
  }
  * { box-sizing: border-box; margin: 0; padding: 0; }
  html, body { width: 1200px; height: 960px; overflow: hidden; }
  body {
    background: var(--backdrop);
    position: relative;
    font-family: "Roboto", Arial, sans-serif;
  }
  .card {
    position: absolute;
    width: 600px;
    height: 343px;
    overflow: hidden;
  }
  /* Front */
  .card-front { left: 314px; top: 113px; background: var(--paper); }
  .brand-dot {
    position: absolute; left: 281px; top: 35px;
    width: 38px; height: 38px; border-radius: 50%;
    background: var(--orange);
  }
  .brand-name {
    position: absolute; left: 0; right: 0; top: 83px;
    text-align: center;
    font-weight: 900; font-size: 40px; letter-spacing: 2px;
    color: var(--ink); line-height: 1;
  }
  .brand-tagline {
    position: absolute; left: 0; right: 0; top: 124px;
    text-align: center;
    font-family: "Roboto Condensed", Arial, sans-serif;
    font-weight: 500; font-size: 13px; letter-spacing: 1px;
    color: var(--ink); text-transform: uppercase;
  }
  .front-arc { position: absolute; left: 0; top: 0; }
  .contact {
    position: absolute; left: 0; right: 0; top: 238px;
    text-align: center; color: var(--white);
  }
  .contact-name {
    font-family: "Roboto Condensed", Arial, sans-serif;
    font-weight: 700; font-size: 25px; line-height: 28px;
  }
  .contact-role { font-size: 16px; line-height: 20px; margin-top: 1px; }
  .contact-email { font-size: 14px; line-height: 18px; }

  /* Back */
  .card-back { left: 311px; top: 472px; background: var(--orange); color: var(--white); }
  .back-mark {
    position: absolute; left: 88px; top: 40px;
    width: 144px; height: 144px; border-radius: 50%;
    background: var(--white);
  }
  .divider {
    position: absolute; left: 263px; top: 30px;
    width: 1px; height: 166px; background: rgba(255,255,255,0.7);
  }
  .offer { position: absolute; left: 297px; top: 31px; width: 295px; }
  .offer-headline {
    font-weight: 700; font-size: 19.5px; line-height: 21px;
    text-transform: uppercase;
  }
  .offer-text { font-size: 15.5px; line-height: 19.5px; margin-top: 6px; }
  .offer-url { font-weight: 700; font-size: 19px; margin-top: 9px; margin-left: -2px; }
  .notes {
    position: absolute; left: 20px; top: 217px;
    width: 557px; height: 101px;
    background: var(--white); border-radius: 16px;
  }
  .note-line {
    position: absolute; left: 24px; right: 28px;
    height: 1px; background: var(--ink);
  }
  .note-line.first { top: 31px; }
  .note-line.second { top: 71px; }
</style>
</head>
<body>
  <section class="card card-front" aria-label="Card front">
    <div class="brand-dot"></div>
    <div class="brand-name">LARKWELL</div>
    <div class="brand-tagline">Make every message count today</div>
    <svg class="front-arc" width="600" height="343" viewBox="0 0 600 343" aria-hidden="true">
      <circle cx="300" cy="562" r="370" fill="var(--orange)"/>
    </svg>
    <div class="contact">
      <div class="contact-name">DANA WHITFIELD</div>
      <div class="contact-role">STORY MARKETING COACH</div>
      <div class="contact-email">dana@larkwellnow.com</div>
    </div>
  </section>

  <section class="card card-back" aria-label="Card back">
    <div class="back-mark"></div>
    <div class="divider"></div>
    <div class="offer">
      <div class="offer-headline">Find more clients.<br>Earn more trust.<br>Build more growth.</div>
      <div class="offer-text">Get your free Larkwell<br>Starter Package and our<br>marketing guide today at</div>
      <div class="offer-url">Larkwellnow.com/start</div>
    </div>
    <div class="notes">
      <div class="note-line first"></div>
      <div class="note-line second"></div>
    </div>
  </section>
</body>
</html>
```